Single-sided business card for restaurant velmora with new logo made on this site

Business card options with new logo including restaurant name, address, phone number and website. This business card is single-sided only and will be presented at the hostess desk for clients to take. I would like to see options based on a cream card background, a white card background, a yellow card background and a burgundy colored background. It needs to be elegant and traditional.

Target Market(s)

local and international crowd

Industry/Entity Type

restaurant

Contact Information for Business Card

address, website and phone number

Font styles to use
Serif

Colors
EE7325
F08F49
F5BC92
FAE3D3
FDF4ED

Requirements
Must have
• new logo, address, phone number, website
Should not have
• more than three colors

```html
<!DOCTYPE html>
<html lang="es">
<head>
<meta charset="utf-8">
<title>Velmora – Tarjeta de presentación</title>
<link rel="stylesheet" href="https://fonts.googleapis.com/css2?family=Marcellus&display=swap">
<style>
  :root {
    --page-bg: #e6e6e6;
    --card-top: #f9bd3f;
    --card-bottom: #f5b12c;
    --ink: #3c1b1d;
    --leaf-soft: rgba(240, 143, 40, 0.45);
  }
  * { margin: 0; padding: 0; box-sizing: border-box; }
  html, body {
    width: 1200px;
    height: 940px;
    overflow: hidden;
    background: var(--page-bg);
  }
  .business-card {
    position: absolute;
    left: 258px;
    top: 275px;
    width: 684px;
    height: 390px;
    border-radius: 18px;
    background: linear-gradient(180deg, var(--card-top), var(--card-bottom));
    overflow: hidden;
    font-family: "Marcellus", serif;
    color: var(--ink);
  }
  .card-frame {
    position: absolute;
    left: 19px;
    top: 17px;
    right: 17px;
    bottom: 17px;
    border: 3.5px solid var(--ink);
  }
  .foliage-decoration {
    position: absolute;
    left: 0;
    top: 40px;
    width: 390px;
    height: 350px;
    background: radial-gradient(ellipse at 45% 75%, var(--leaf-soft) 0%, rgba(240, 143, 40, 0.15) 45%, rgba(240, 143, 40, 0) 72%);
  }
  .brand {
    position: absolute;
    left: 476px;
    top: 41px;
    width: 180px;
    text-align: center;
  }
  .brand-square {
    display: block;
    width: 83px;
    height: 83px;
    margin: 0 auto;
    background: var(--ink);
  }
  .brand-name {
    display: block;
    margin-top: 20px;
    font-size: 27px;
    font-weight: 400;
    letter-spacing: 4px;
    padding-left: 4px;
    line-height: 1;
    color: var(--ink);
  }
  .contact {
    position: absolute;
    left: 48px;
    top: 200px;
  }
  .address {
    font-style: normal;
    font-size: 15.5px;
    line-height: 19.2px;
    letter-spacing: 0.2px;
  }
  .reservations-label {
    margin-top: 7px;
    font-size: 15.5px;
    line-height: 19px;
    letter-spacing: 0.2px;
  }
  .phone {
    margin-top: 3px;
    font-size: 21px;
    line-height: 24px;
  }
  .website {
    margin-top: 8px;
    font-size: 14.5px;
    line-height: 18px;
    letter-spacing: 0.4px;
  }
</style>
</head>
<body>
  <div class="business-card">
    <div class="foliage-decoration" role="img" aria-label="Faint botanical leaf decoration in warm orange tones"></div>
    <div class="card-frame"></div>

    <div class="brand">
      <span class="brand-square"></span>
      <span class="brand-name">VELMORA</span>
    </div>

    <div class="contact">
      <address class="address">
        Restaurant Velmora<br>
        Jacaranda 418<br>
        Bahías de Solmar<br>
        Costa Azul CP 70412
      </address>
      <p class="reservations-label">Reservaciones</p>
      <p class="phone">958-555-0142</p>
      <p class="website">www.velmora.com.mx</p>
    </div>
  </div>
</body>
</html>
```